Business Card for a Jewellery Brand

Business card for an upscale jewellery brand. Attached is the brand logo and icon and color board. I am looking for two card versions: one for the founder and one is generic. The card should be elegant and convey upscale and premium feel. I am open to both square and rectangle card shapes.

Industry/Entity Type

Jewelry

Contact Information for Business Card

Two cards: (1) Sunela Parvaniya (Founder) (2) General
(1) Sunela Parvaniya card should have Name: Sunela Parvaniya, Title: Founder Email id: sunela@quiremo.com.au. Phone no: +61452913307
(2) Generic card should have Email id: info@quiremo.com.au. Phone no: +61436207518

Requirements
Must have
• Workmark
• ICON
• Phone no
• Email ID
• ABN: 58219740312 (Note: ABN is Business number in Australia)
• Website: www.quiremo.com.au
• Instagram: quiremo_jewellery
• Facebook: @quiremojewellery
Nice to have
• Tagline

```html
<!DOCTYPE html>
<html lang="en">
<head>
<meta charset="utf-8">
<title>Quiremo Business Card</title>
<link href="https://fonts.googleapis.com/css2?family=Jost:wght@400;500&family=Poppins:wght@400&display=swap" rel="stylesheet">
<style>
  :root {
    --bg: #141414;
    --rose: #e59a96;
    --ink: #2b2b2b;
    --paper: #ffffff;
  }
  html, body {
    margin: 0;
    padding: 0;
    width: 1200px;
    height: 900px;
    overflow: hidden;
    background: var(--bg);
  }
  .canvas {
    position: relative;
    width: 1200px;
    height: 900px;
  }
  .card {
    position: absolute;
    top: 150px;
    width: 343px;
    height: 601px;
  }
  .card--front {
    left: 246px;
    background: var(--paper);
  }
  .card--back {
    left: 611px;
    background: var(--rose);
  }
  .holder-name {
    position: absolute;
    left: 47px;
    top: 38px;
    margin: 0;
    font: 400 19px/1 "Jost", sans-serif;
    letter-spacing: 0.5px;
    text-transform: uppercase;
    color: var(--rose);
  }
  .holder-title {
    position: absolute;
    left: 47px;
    top: 63px;
    margin: 0;
    font: 500 15px/1 "Jost", sans-serif;
    letter-spacing: 0.3px;
    color: var(--ink);
  }
  .detail {
    position: absolute;
    left: 47px;
    margin: 0;
    font: 400 14px/1 "Poppins", sans-serif;
    letter-spacing: 0.6px;
    color: var(--ink);
  }
  .detail .label { color: var(--rose); }
  .abn { top: 113px; }
  .front-wordmark {
    position: absolute;
    left: 47px;
    width: 180px;
    top: 262px;
    margin: 0;
    text-align: center;
    font: 400 32px/1 "Jost", sans-serif;
    letter-spacing: 4px;
    color: var(--rose);
  }
  .contact-list {
    position: absolute;
    left: 47px;
    top: 433px;
    margin: 0;
    padding: 0;
    list-style: none;
  }
  .contact-list li {
    display: flex;
    align-items: center;
    height: 21.5px;
    font: 400 14px/1 "Poppins", sans-serif;
    letter-spacing: 0.6px;
    color: var(--ink);
  }
  .contact-list svg {
    width: 14px;
    height: 14px;
    margin-right: 13px;
    fill: none;
    stroke: var(--rose);
    stroke-width: 1.8;
  }
  .social-ins { top: 528px; }
  .social-fb { top: 550px; }
  .brand-mark {
    position: absolute;
    left: 50%;
    top: 240px;
    width: 58px;
    height: 58px;
    margin-left: -29px;
    border-radius: 50%;
    background: var(--paper);
  }
  .brand-wordmark {
    position: absolute;
    left: 0;
    right: 0;
    top: 336px;
    margin: 0;
    text-align: center;
    font: 400 40px/1 "Jost", sans-serif;
    letter-spacing: 8px;
    padding-left: 8px;
    color: var(--paper);
  }
</style>
</head>
<body>
<main class="canvas">
  <section class="card card--front">
    <h1 class="holder-name">Sunela Parvaniya</h1>
    <p class="holder-title">FOUNDER</p>
    <p class="detail abn"><span class="label">ABN:</span> 58219740312</p>
    <p class="front-wordmark">QUIREMO</p>
    <ul class="contact-list">
      <li>
        <svg viewBox="0 0 14 14"><rect x="3" y="0.9" width="8" height="12.2" rx="1.2"/><line x1="6" y1="11" x2="8" y2="11"/></svg>
        +61452913307
      </li>
      <li>
        <svg viewBox="0 0 14 14"><rect x="0.9" y="3" width="12.2" height="8.5" fill="var(--rose)"/><polyline points="1,3.5 7,8 13,3.5" stroke="#fff" stroke-width="1.2"/></svg>
        www.quiremo.com.au
      </li>
      <li>
        <svg viewBox="0 0 14 14"><circle cx="6" cy="6" r="4.2"/><line x1="9" y1="9" x2="13" y2="13"/></svg>
        sunela@quiremo.com.au.
      </li>
    </ul>
    <p class="detail social-ins"><span class="label">Ins:</span> quiremo_jewellery</p>
    <p class="detail social-fb"><span class="label">Fb:</span> @quiremojewellery</p>
  </section>

  <section class="card card--back">
    <div class="brand-mark" aria-hidden="true"></div>
    <p class="brand-wordmark">QUIREMO</p>
  </section>
</main>
</body>
</html>
```